New business card for a regional office of a US M&A company

We need business card for a finance company, office based in Hong Kong , our Head office is in US, our business is to Merge and acquires companies , the new office will be a regional office for the Asia Pacific region. We want to use the head office logo as attached ( but don't have to be exactly the same, can be a variation to it) as a base and then add Asia Pacific alongside the logo.
We would prefer to have be bilingual Eng + Chinese, although we don't really have Chinese company name .

Industry/Entity Type

Business

Contact Information for Business Card

Clara Jo Tsang
 

VP,
APAC M&A Operations
Eli Global Asia Pacific Limited
 
Unit 1407, K18
18 Tai Lok Shan Road, 
Hong Kong 
 
M: +852 6038 1742
T : +852 2836 4100
F : +852 2836 4177
VOIP: 4158
 
cjtsang@orinvantage.com

Font styles to use
Serif
Sans Serif

Colors

Designer to choose colors to be used in the design.

Requirements
Must have
• APAC Office

```html
<!DOCTYPE html>
<html lang="en">
<head>
<meta charset="utf-8">
<title>Orin Vantage Asia Pacific – Business Card</title>
<link href="https://fonts.googleapis.com/css2?family=Ubuntu:wght@400;500;700&display=swap" rel="stylesheet">
<style>
  :root {
    --page-bg: #e6e3df;
    --card-bg: #f1f2f1;
    --card-edge: #d3d6d6;
    --teal: #1f8ea3;
    --teal-deep: #17768a;
    --ink: #2a2e33;
  }
  * { margin: 0; padding: 0; box-sizing: border-box; }
  html, body {
    width: 1200px; height: 1010px; overflow: hidden;
    background: var(--page-bg);
    font-family: "Ubuntu", Arial, sans-serif;
  }
  .card {
    position: absolute; left: 80px; top: 205px;
    width: 1040px; height: 600px;
    background: var(--card-bg);
    border: 1px solid var(--card-edge);
  }
  .brand {
    position: absolute; left: 40px; top: 0; width: 400px; height: 600px;
    display: flex; align-items: center; justify-content: center; gap: 18px;
  }
  .brand-mark { width: 52px; height: 52px; background: var(--teal); }
  .brand-name { font-weight: 700; font-size: 36px; color: var(--teal); }
  .details { position: absolute; left: 523px; top: 0; color: var(--ink); }
  .person-name {
    position: absolute; top: 95px; white-space: nowrap;
    font-weight: 700; font-size: 39px; color: var(--teal);
  }
  .person-title {
    position: absolute; top: 156px; width: 400px;
    font-size: 22px; line-height: 31px;
  }
  .company {
    position: absolute; top: 274px; white-space: nowrap;
    font-weight: 700; font-size: 30px; color: var(--teal);
  }
  .contacts { position: absolute; top: 322px; list-style: none; width: 480px; }
  .contacts li {
    display: flex; align-items: center; height: 30.5px;
    font-size: 23px; white-space: nowrap;
  }
  .contacts svg { width: 18px; height: 18px; margin: 0 17px 0 8px; fill: var(--teal); }
  .label { color: var(--teal); }
  .address {
    position: absolute; top: 448px; width: 420px;
    font-size: 23px; line-height: 31px;
  }
</style>
</head>
<body>
  <div class="card">
    <div class="brand">
      <span class="brand-mark"></span>
      <span class="brand-name">Orin Vantage</span>
    </div>
    <div class="details">
      <h1 class="person-name">Clara Jo Tsang</h1>
      <p class="person-title">Vice President,<br>APAC M&amp;A Operations</p>
      <h2 class="company">Orin Vantage Asia Pacific Limited</h2>
      <ul class="contacts">
        <li><svg viewBox="0 0 18 18" aria-hidden="true"><path d="M5 1h8a1 1 0 0 1 1 1v14a1 1 0 0 1-1 1H5a1 1 0 0 1-1-1V2a1 1 0 0 1 1-1zm1 2v10h6V3zm3 11.2a1 1 0 1 0 0 .1z"/></svg>+852 6038 1742</li>
        <li><svg viewBox="0 0 18 18" aria-hidden="true"><path d="M1 6c0-2 3-3 8-3s8 1 8 3v1.5h-4V6H5v1.5H1zM4 9h10l2 6H2zm5 1.5a2 2 0 1 0 0 4 2 2 0 0 0 0-4z"/></svg>+852 2836 4100</li>
        <li><svg viewBox="0 0 18 18" aria-hidden="true"><path d="M5 1h8v5H5zM2 7h14v7h-3v3H5v-3H2zm4 5v3h6v-3z"/></svg>+852 2836 4177,&nbsp; <span class="label">VOIP</span>: 4158</li>
        <li><svg viewBox="0 0 18 18" aria-hidden="true"><path d="M1 4h16v1.2L9 10 1 5.2zm0 2.6 8 4.8 8-4.8V14H1z"/></svg>cjtsang@orinvantage.com</li>
      </ul>
      <p class="address">Unit 1407, K18 18, Tai Lok Shan<br>Road, Hong Kong</p>
    </div>
  </div>
</body>
</html>
```